Business Card Design for company

We want new business cards. We'd like something different-- yet still highly professional. Our tagline is Providing leadership, delivering success. Stock photos are ok, as long as they are relevant and look upscale.

Target Market(s)

Architecture/Business Management Consulting/Engineering Consulting

Contact Information for Business Card

dark gray background with pops of blue might be good, but you tell me. You're the designers. Rounded corners might be nice, but again, you tell me.

Font styles to use
Serif
Sans Serif

Colors
3276b5
5c5c5c
9d9d9d
fbfbfb

Requirements
Nice to have
• Something different, but still very professional.

```html
<!DOCTYPE html>
<html lang="en">
<head>
<meta charset="utf-8">
<title>Arvell Group – Business Card</title>
<link rel="stylesheet" href="https://fonts.googleapis.com/css2?family=Montserrat:wght@300;400;600&display=swap">
<style>
  :root {
    --brand-blue: #3276b5;
    --blue-deep: #245e96;
    --charcoal: #5c5c5c;
    --charcoal-dark: #3f4144;
    --silver: #9d9d9d;
    --paper: #fbfbfb;
    --backdrop: #1e1f21;
  }
  html, body {
    margin: 0;
    width: 1200px;
    height: 900px;
    overflow: hidden;
    background: var(--backdrop);
    font-family: "Montserrat", sans-serif;
  }
  .canvas { position: relative; width: 1200px; height: 900px; }
  .card {
    position: absolute;
    width: 620px;
    height: 354px;
    border-radius: 26px;
    overflow: hidden;
    box-shadow: 0 18px 40px rgba(0,0,0,.55);
  }
  .card svg { display: block; width: 100%; height: 100%; }
  .card--front { left: 110px; top: 50px; }
  .card--back { left: 470px; top: 496px; }
  .brand-name { font-family: "Montserrat", sans-serif; font-weight: 600; font-size: 38px; letter-spacing: 2px; }
  .brand-name--back { font-size: 26px; letter-spacing: 1.5px; }
  .tagline { font-weight: 300; font-size: 15px; fill: var(--paper); letter-spacing: .5px; }
  .website { font-weight: 300; font-size: 14px; fill: var(--paper); letter-spacing: 4px; }
  .person-name { font-size: 24px; fill: var(--paper); letter-spacing: .5px; }
  .person-name .strong { font-weight: 600; }
  .person-name .light { font-weight: 300; }
  .job-title { font-weight: 300; font-size: 13px; fill: #d8d8d8; }
  .contact-text { font-weight: 400; font-size: 11.5px; fill: #444; }
</style>
</head>
<body>
<main class="canvas">

  <section class="card card--front" aria-label="Business card front">
    <svg viewBox="0 0 620 354" xmlns="http://www.w3.org/2000/svg">
      <defs>
        <linearGradient id="charcoalFront" x1="0" y1="0" x2="1" y2="1">
          <stop offset="0" stop-color="#55585c"/>
          <stop offset="1" stop-color="#3d3f42"/>
        </linearGradient>
      </defs>
      <rect width="620" height="354" fill="url(#charcoalFront)"/>
      <path class="swoosh-shade" d="M62 354 C150 262 300 200 620 176 L620 196 C330 215 180 280 100 354 Z" fill="var(--blue-deep)"/>
      <path class="swoosh" d="M30 354 C110 250 280 180 620 150 L620 182 C320 200 160 268 70 354 Z" fill="var(--brand-blue)"/>

      <g class="logo-lockup">
        <rect x="188" y="72" width="22" height="22" fill="var(--brand-blue)"/>
        <text class="brand-name" x="222" y="95" fill="var(--paper)">Arvell Group</text>
      </g>
      <text class="tagline" x="310" y="132" text-anchor="middle">Providing leadership, Delivering success</text>
      <text class="website" x="380" y="270" text-anchor="middle">www.yourwebsite.com</text>
    </svg>
  </section>

  <section class="card card--back" aria-label="Business card back">
    <svg viewBox="0 0 620 354" xmlns="http://www.w3.org/2000/svg">
      <defs>
        <linearGradient id="charcoalBack" x1="0" y1="0" x2="1" y2="1">
          <stop offset="0" stop-color="#55585c"/>
          <stop offset="1" stop-color="#3d3f42"/>
        </linearGradient>
      </defs>
      <rect width="620" height="354" fill="url(#charcoalBack)"/>
      <path class="band-shade" d="M118 354 C190 232 320 168 620 138 L620 172 C330 195 210 250 150 354 Z" fill="var(--blue-deep)"/>
      <path class="band" d="M128 354 C200 240 330 176 620 140 L620 172 C330 200 220 250 162 354 Z" fill="var(--brand-blue)"/>
      <path class="info-panel" d="M158 354 C222 252 336 202 620 170 L620 354 Z" fill="var(--paper)"/>

      <text class="person-name" x="310" y="78" text-anchor="middle"><tspan class="strong">YOUR</tspan><tspan class="light"> NAME</tspan></text>
      <text class="job-title" x="310" y="100" text-anchor="middle">Job Title</text>

      <text class="brand-name brand-name--back" x="445" y="262" text-anchor="middle" fill="var(--charcoal)">Arvell Group</text>

      <g class="contact contact--phone">
        <circle cx="202" cy="318" r="10" fill="var(--brand-blue)"/>
        <path d="M197.5 313 q-1 6 5 11 q2 1 4 -1 l-2 -3 l-2 1 q-2 -2 -3 -4 l1 -2 l-2 -3 q-1 0 -1 1 Z" fill="var(--paper)"/>
        <text class="contact-text" x="217" y="322">000 000 0000</text>
      </g>
      <g class="contact contact--email">
        <circle cx="316" cy="318" r="10" fill="var(--brand-blue)"/>
        <rect x="310.5" y="314" width="11" height="8" fill="var(--paper)"/>
        <path d="M310.5 314 L316 319 L321.5 314" fill="none" stroke="var(--brand-blue)" stroke-width="1.2"/>
        <text class="contact-text" x="331" y="322">youremail@xzy.com</text>
      </g>
      <g class="contact contact--address">
        <circle cx="468" cy="318" r="10" fill="var(--brand-blue)"/>
        <path d="M468 325 C464 320 463.8 317.5 463.8 315.5 a4.2 4.2 0 0 1 8.4 0 C472.2 317.5 472 320 468 325 Z" fill="var(--paper)"/>
        <circle cx="468" cy="315.5" r="1.5" fill="var(--brand-blue)"/>
        <text class="contact-text" x="483" y="322">your address here</text>
      </g>
    </svg>
  </section>

</main>
</body>
</html>
```